Luxury Wine Label for New Startup Winery

We need a wine label for our new winery startup. We have worked with a local designer but do not feel the resulting label / logo have the elevation required to present our brand as a luxury wine. Our winery is called "Quailbrook Vineyards" and we are focused on extremely high quality hand crafted artisan and estate wines from the Pacific Northwest.
We would like to see designs that utilize a tree line, or other imagery that represents the "Quailbrook" part of our company name. Another interesting feature could be wood grain.
A logo will be required based on your design so please design with this in mind:
This logo should be consistent with the wine bottle label design, and should be representative of our high end exclusive wine while giving a sense of place (Oregon/ Pacific Northwest.)
I will supply an image of the design we received from our local designer, PLEASE NOTE: in general we do like wood grain and tree line concepts but feel the execution was poorly done.
ATTN: Logo design should be suitable for use on: Bottles (Red wine/rose/white wine), Bussiness cards, vehicle signage, business signage, etc
P.S.:
If you have a design that is not outside the box we are still interested in seeing it.
Label is for a burgundy style bottle with a label height of 3.5 - 4" and a width of 3.5-4"
any label <= 4"x4" and >=3.5"x3.5" will be acceptable:
HOWEVER Width should be greater than or equal to height due to the bottle format
Target Market(s)
Wine enthusiasts with adequate discretionary budgets to afford $100 bottles of wine.
Industry/Entity Type
Wine / Winery
Requirements
Must have
- A sense of luxury, a feel of exclusivity, and a theme consistent with our product and brand name
Nice to have
- Tree line, wood grain or other wood themes. Serif fonts
Should not have
- anything cheesy, off topic, hard to read script fonts or anything that makes the label hard to read from a few feet away or too busy

```html
<!DOCTYPE html>
<html lang="en">
<head>
<meta charset="utf-8">
<title>Quailbrook Vineyards – Syrah Label</title>
<link rel="stylesheet" href="https://fonts.googleapis.com/css2?family=Libre+Caslon+Text&family=Roboto+Slab:wght@400&display=swap">
<style>
  :root {
    --canvas: #f6f3ea;
    --label-black: #000000;
    --white: #ffffff;
    --gold: #c9a545;
    --gold-light: #f8ee9a;
    --gold-deep: #c99a3a;
    --silver-dark: #5e5e5e;
    --silver-mid: #b8b8b8;
    --silver-light: #ffffff;
    --wood-dark: #3e2a1a;
    --wood-mid: #6b4a30;
    --ink-dark: #2b2112;
  }
  * { margin: 0; padding: 0; box-sizing: border-box; }
  html, body {
    width: 1200px; height: 1200px; overflow: hidden;
    background: var(--canvas);
  }
  .canvas {
    position: relative; width: 1200px; height: 1200px;
  }
  .main-label {
    position: absolute; left: 133px; top: 101px;
    width: 934px; height: 758px;
    background: var(--label-black);
  }
  .silver-band {
    position: absolute; left: 0; width: 100%; height: 58px;
    background: linear-gradient(90deg, var(--silver-dark) 0%, var(--silver-mid) 22%, var(--silver-light) 50%, var(--silver-mid) 78%, var(--silver-dark) 100%);
  }
  .silver-band--top { top: 0; }
  .silver-band--bottom { top: 700px; }
  .winery-name {
    position: absolute; left: 0; width: 100%; top: 188px;
    text-align: center; color: var(--white);
    font-family: "Libre Caslon Text", serif;
    font-size: 78px; line-height: 72px; letter-spacing: 3px;
  }
  .region {
    position: absolute; left: 0; width: 100%; top: 368px;
    text-align: center; color: var(--gold);
    font-family: "Roboto Slab", serif;
    font-size: 35px; letter-spacing: 4px;
  }
  .wine-type {
    position: absolute; left: 0; width: 100%; top: 418px;
    display: flex; justify-content: center; align-items: center; gap: 26px;
    color: var(--white);
    font-family: "Roboto Slab", serif;
    font-size: 35px; letter-spacing: 3px;
  }
  .wine-type .rule { width: 106px; height: 3px; background: var(--white); }
  .tree-line {
    position: absolute; left: 0; top: 493px; width: 100%; height: 155px;
  }
  .gold-stripe {
    position: absolute; left: 0; width: 100%; height: 15px;
    background: var(--gold-deep);
  }
  .gold-stripe--upper { top: 655px; }
  .gold-stripe--lower { top: 676px; }

  .varietal-band {
    position: absolute; left: 133px; top: 894px;
    width: 934px; height: 205px;
  }
  .gold-band {
    position: absolute; left: 0; width: 100%; height: 30px;
    background: linear-gradient(90deg, var(--gold-light) 0%, var(--gold-deep) 30%, var(--gold-light) 62%, var(--gold-deep) 100%);
  }
  .gold-band--top { top: 0; }
  .gold-band--bottom {
    top: 175px;
    display: flex; justify-content: center; align-items: center;
    color: var(--ink-dark);
    font-family: "Roboto Slab", serif; font-size: 21px; letter-spacing: 2px;
  }
  .wood-panel {
    position: absolute; left: 0; top: 30px; width: 100%; height: 145px;
  }
  .varietal {
    position: absolute; left: 0; top: 30px; width: 100%; height: 145px;
    display: flex; justify-content: center; align-items: center;
    color: var(--white);
    font-family: "Libre Caslon Text", serif; font-size: 76px; letter-spacing: 6px;
  }
</style>
</head>
<body>
<div class="canvas">
  <section class="main-label">
    <div class="silver-band silver-band--top"></div>
    <h1 class="winery-name">QUAILBROOK<br>VINEYARDS</h1>
    <p class="region">“WILLAMETTE VALLEY”</p>
    <p class="wine-type"><span class="rule"></span>ROSE WINE<span class="rule"></span></p>
    <svg class="tree-line" role="img" aria-label="Gold evergreen tree line silhouette" viewBox="0 0 934 155" preserveAspectRatio="none">
      <defs>
        <linearGradient id="treeGold" x1="0" y1="0" x2="0" y2="1">
          <stop offset="0" stop-color="#5a4a1c"/>
          <stop offset="0.35" stop-color="#e9d978"/>
          <stop offset="1" stop-color="#c99a3a"/>
        </linearGradient>
      </defs>
      <rect width="934" height="155" fill="url(#treeGold)"/>
    </svg>
    <div class="gold-stripe gold-stripe--upper"></div>
    <div class="gold-stripe gold-stripe--lower"></div>
    <div class="silver-band silver-band--bottom"></div>
  </section>

  <section class="varietal-band">
    <div class="gold-band gold-band--top"></div>
    <svg class="wood-panel" role="img" aria-label="Dark walnut wood grain" viewBox="0 0 934 145" preserveAspectRatio="none">
      <defs>
        <linearGradient id="woodTone" x1="0" y1="0" x2="0" y2="1">
          <stop offset="0" stop-color="#4a3220"/>
          <stop offset="0.5" stop-color="#6b4a30"/>
          <stop offset="1" stop-color="#3e2a1a"/>
        </linearGradient>
      </defs>
      <rect width="934" height="145" fill="url(#woodTone)"/>
    </svg>
    <h2 class="varietal">SYRAH</h2>
    <div class="gold-band gold-band--bottom">ESTATE | 2023 | GROWN</div>
  </section>
</div>
</body>
</html>
```